Corporate-Design für Steuerberatungsgesellschaft
Zielgruppe
Wir sind eine Steuerberatungsgesellschaft mit 10 Mitarbeitern im Norden von Deutschland, kurz vor der Ostseeküste. Unser Unternehmen besteht seit 30 Jahren. Wir betreuen vor allem Mandanten in kleinen und mittleren Unternehmen: von der Arztpraxis bis zum Bauunternehmen. Demnächst werden wir neue Räume beziehen. Diese sollen großzügiger und moderner werden, teilweise mit Glaswänden.
Aufgabenstellung
Unser bisheriges Farbkonzept war von bordeaux und creme geprägt (www.kanzlei-mervato.de). Das muss aber nicht weiter bestehen. Das bisherige Logo finden wir inhaltlich recht treffend, aber es sollte moderner gestaltet werden. Der Schriftzug des Kanzleinamens soll an der Fassade in silbernen Buchstaben angebracht werden.

```html
<!DOCTYPE html>
<html lang="de">
<head>
<meta charset="utf-8">
<title>Mervato Steuerberatung – Corporate Design</title>
<link rel="stylesheet" href="https://fonts.googleapis.com/css2?family=Noto+Serif:wght@400;700&display=swap">
<style>
  :root{
    --bordeaux:#9b1b2a;
    --anthracite:#3a3a3c;
    --card-dark:#545456;
    --paper:#ffffff;
    --stage-grey:#c9c9cb;
    --stage-mint:#e3e8e3;
    --text:#333335;
    --muted:#6a6a6c;
  }
  *{box-sizing:border-box;margin:0;padding:0}
  html,body{width:1200px;height:2416px;overflow:hidden}
  body{font-family:"Noto Serif",Georgia,serif;color:var(--text);background:var(--paper);position:relative}

  .brand{display:flex;align-items:center;gap:14px;font-weight:700;color:var(--bordeaux);letter-spacing:.04em;white-space:nowrap}
  .brand-square{display:block;background:var(--bordeaux);flex:none}

  /* Section 1 – wordmark */
  .logo-stage{position:absolute;left:0;top:0;width:1200px;height:570px;display:flex;align-items:center;justify-content:center}
  .logo-stage .brand{font-size:60px}
  .logo-stage .brand-square{width:46px;height:46px}

  /* Section 2 – business cards */
  .card-stage{position:absolute;left:0;top:570px;width:1200px;height:915px;background:var(--stage-grey)}
  .card{position:absolute;width:470px;height:290px;overflow:hidden}
  .card-back{left:95px;top:190px;background:var(--card-dark);color:#fff}
  .card-back .brand{position:absolute;left:0;right:0;top:100px;justify-content:center;font-size:30px;color:#fff}
  .card-back .brand-square{width:24px;height:24px}
  .card-back .services{position:absolute;left:34px;bottom:34px;font-size:11px;line-height:1.55;color:#e6e6e6}
  .card-rule{position:absolute;left:0;right:0;bottom:16px;height:4px;background:var(--bordeaux)}
  .card-back .card-rule{right:110px}

  .card-front{left:635px;top:420px;background:var(--paper)}
  .card-front .person{position:absolute;left:32px;top:34px;font-size:11px;line-height:1.45;color:var(--text)}
  .card-front .person .name{font-size:19px;font-weight:700;color:var(--bordeaux);line-height:1.3}
  .card-front .company{position:absolute;left:260px;top:120px;font-size:10.5px;line-height:1.5}
  .card-front .company strong{font-weight:700}
  .card-front .company .firm{color:var(--bordeaux)}
  .card-front .contact{position:absolute;left:260px;top:196px;font-size:10px;line-height:1.7;list-style:none}
  .card-front .contact li,.letter .contact li{display:flex;align-items:center;gap:7px}
  .icon{width:9px;height:9px;border-radius:50%;background:var(--bordeaux);flex:none}
  .card-front .card-rule{left:150px}

  /* Section 3 – letterhead */
  .letter-stage{position:absolute;left:0;top:1485px;width:1200px;height:931px;background:var(--stage-mint)}
  .letter{position:absolute;left:310px;top:78px;width:540px;height:772px;background:var(--paper)}
  .letter .brand{position:absolute;right:22px;top:30px;font-size:26px}
  .letter .brand-square{width:20px;height:20px}
  .letter .sender{position:absolute;left:58px;top:198px;font-size:7px;line-height:1.5}
  .letter .sender strong{font-weight:700}
  .sender-rule{position:absolute;left:0;top:223px;width:178px;height:1.5px;background:var(--bordeaux)}
  .letter .contact{position:absolute;left:352px;top:185px;list-style:none;font-size:8.5px;line-height:1.6}
  .letter .contact .icon{width:8px;height:8px}
  .contact-rule{position:absolute;left:352px;right:0;top:256px;height:1.5px;background:var(--bordeaux)}
  .letter .management{position:absolute;left:352px;top:266px;font-size:8.5px;line-height:1.55}
  .letter .management strong{font-weight:700}
  .fold-mark{position:absolute;left:0;top:278px;width:6px;height:1px;background:var(--bordeaux)}
  .fold-mark.second{top:478px}
  .letter-footer{position:absolute;left:0;right:0;bottom:0;height:68px;background:var(--bordeaux);color:#f2dfe1;font-size:6.5px;line-height:2.45;padding:8px 58px}
  .letter-footer strong{font-weight:700;color:#fff}
</style>
</head>
<body>

<section class="logo-stage">
  <div class="brand"><span class="brand-square"></span>Mervato Steuerberatung</div>
</section>

<section class="card-stage">
  <article class="card card-back">
    <div class="brand"><span class="brand-square"></span>Mervato Steuerberatung</div>
    <p class="services">Steuerberatung, Finanz- und Lohnbuchhaltung<br>Betriebswirtschaftliche Beratung</p>
    <div class="card-rule"></div>
  </article>

  <article class="card card-front">
    <div class="person">
      Diplom-Kaufmann
      <div class="name">Jonas Behrendt - Lukow</div>
      Geschäftsführer / Steuerberater
    </div>
    <div class="company">
      <strong><span class="firm">Mervato</span></strong><br>
      <strong>Steuerberatungsgesellschaft mbH</strong><br>
      Lindenhofweg 4<br>
      D - 17390 Bredenau
    </div>
    <ul class="contact">
      <li><span class="icon"></span>+49 (0) 30418 / 52 61 - 0</li>
      <li><span class="icon"></span>+49 (0) 30418 / 52 61 - 49</li>
      <li><span class="icon"></span>kontakt@kanzlei-mervato.de</li>
      <li><span class="icon"></span>www.kanzlei-mervato.de</li>
    </ul>
    <div class="card-rule"></div>
  </article>
</section>

<section class="letter-stage">
  <article class="letter">
    <div class="brand"><span class="brand-square"></span>Mervato Steuerberatung</div>

    <p class="sender"><strong>Mervato Steuerberatungsgesellschaft mbH</strong><br>Lindenhofweg 4 • D - 17390 Bredenau</p>
    <div class="sender-rule"></div>

    <ul class="contact">
      <li><span class="icon"></span>+49 (0) 30418 / 52 61-0</li>
      <li><span class="icon"></span>+49 (0) 30418 / 52 61-49</li>
      <li><span class="icon"></span>kontakt@kanzlei-mervato.de</li>
      <li><span class="icon"></span>www.kanzlei-mervato.de</li>
    </ul>
    <div class="contact-rule"></div>

    <p class="management">
      Geschäftsführer:<br>
      <strong>Jonas Behrendt - Lukow</strong><br>
      Steuerberater / Dipl. Kaufmann<br>
      <strong>Till Oberbeck</strong><br>
      Steuerberater
    </p>

    <div class="fold-mark"></div>
    <div class="fold-mark second"></div>

    <footer class="letter-footer">
      <strong>Mervato Steuerberatungsgesellschaft mbH</strong> • Lindenhofweg 4 • D - 17390 Bredenau<br>
      <strong>USt-IdNr.</strong> DE000000000 • AG Bredenau • HRB 4718<br>
      Kreissparkasse Bredenau • <strong>IBAN</strong> DE00 0000 0000 0000 0000 00 • <strong>BIC</strong> NOLADE21BRD
    </footer>
  </article>
</section>

</body>
</html>
```